Stationery Design

Need a stationery design for an established accounting firm based in London, England.

The company’s name is ‘Marcus Thorne’. We provide a broad range of bookkeeping, accounting, audit, tax and business services to a wide range of clients (ie, individuals, company, partnerships, etc).

The stationary design needs to show strength and trust and should be clean, corporate and professional.

Only 2 colours must be used as noted on the logo.

The fonts are in Optima

We need the following:

#1: Business Cards (design on 2 sides)
#2: Letterhead (word format) and can be sent to printers
#3: Continuation sheets (word format) and can be sent to printers
#4: Sales invoice template (word format) and can be sent to printers
#5: Report Cover front and back for binding,
#6: Complimentary Slips,
#7: Legal corners with our logo only
#7: Email signature templates

I have attached my company's logo in various file formats

We also need to have our accountancy association’s logo and this must be in the same colour as the dark blue. This IFRB logo must be at least 8mm square (can be larger). I have attached the IFRB logo in various file formats

I have also attached other information that you will need for the letter head and invoice templates

I have also attached our old letterhead, fee note template for reference
Updates

Dear Designers - I have increased the budget

Dear Designers - I have read your comments on the fact that the prize does not reflect the work. Thank you and I appreciate your comments. Unfortunately, I am a start up and my budget is limited. As an Alternative, I have reduced the work that I am asking for to the following items and I hope you can assist: #1: Business Cards (design on 2 sides) #2: Letterhead (word format) and can be sent to printers #3: Report Cover front and back for binding, #4: Email signature templates Regards

Industry/Entity Type

Accounting

```html
<!DOCTYPE html>
<html lang="en">
<head>
<meta charset="utf-8">
<title>Marcus Thorne – Email Signature</title>
<link href="https://fonts.googleapis.com/css2?family=Tenor+Sans&family=Source+Sans+3:ital,wght@0,400;1,400&display=swap" rel="stylesheet">
<style>
  :root {
    --navy: #1f2f5e;
    --plum: #8a2a7a;
    --text-grey: #6b6b6b;
    --rule-grey: #a9a9a9;
    --paper: #ffffff;
  }
  html, body {
    margin: 0;
    padding: 0;
    width: 1200px;
    height: 1000px;
    overflow: hidden;
    background: var(--paper);
  }
  .signature {
    position: absolute;
    left: 155px;
    top: 300px;
    width: 890px;
  }
  .brand {
    display: flex;
    align-items: center;
    gap: 26px;
    height: 88px;
  }
  .brand-mark {
    width: 64px;
    height: 64px;
    background: var(--navy);
  }
  .brand-name {
    font-family: "Tenor Sans", sans-serif;
    font-size: 48px;
    letter-spacing: 1px;
    color: var(--navy);
    text-transform: uppercase;
  }
  .person-name {
    margin: 34px 0 0;
    font-family: "Source Sans 3", sans-serif;
    font-weight: 400;
    font-size: 52px;
    line-height: 1.05;
    color: var(--navy);
  }
  .person-role {
    margin: 4px 0 0;
    font-family: "Source Sans 3", sans-serif;
    font-style: italic;
    font-size: 33px;
    color: var(--plum);
  }
  .divider {
    margin: 16px 0 18px;
    height: 0;
    border-top: 3px solid var(--rule-grey);
  }
  .contact {
    display: flex;
    font-family: "Source Sans 3", sans-serif;
    font-size: 22px;
    line-height: 32px;
    color: var(--text-grey);
  }
  .contact-address { width: 600px; margin: 0; font-style: normal; }
  .contact-lines { margin: 0; padding: 0; list-style: none; }
</style>
</head>
<body>
  <section class="signature">
    <div class="brand">
      <div class="brand-mark"></div>
      <span class="brand-name">Marcus Thorne</span>
    </div>
    <h1 class="person-name">Oliver Hale</h1>
    <p class="person-role">Managing partner</p>
    <div class="divider"></div>
    <div class="contact">
      <address class="contact-address">
        12 Linden Court,<br>
        Wexmoor Business Park,<br>
        Ashgrove Road, Elmstead Green,<br>
        Middlesex HA4 7QT
      </address>
      <ul class="contact-lines">
        <li>T: 020 7946 0381</li>
        <li>F: 020 7946 0382</li>
        <li>E: mail@marcusthorne.co.uk</li>
        <li>W: www.marcusthorne.co.uk</li>
      </ul>
    </div>
  </section>
</body>
</html>
```